Valdrin Insight Powerpoint

Take an outdated PowerPoint and modernize it to our company's brand via google PowerPoint. Please check out our website at www.valdrinpartners-example.com to see more styles but give it that intelligence twist. The powerpoint to work on is the Insight PP. Please keep it professional.

Target Market(s)

Security Industry / Silicon Valley

Industry/Entity Type

Executive Protection / Intelligence

Requirements
Must have
• Valdrin Logo / Valdrin Colors / Confidential notice at bottom
Nice to have
• Pictures of major cities / San Francisco
Should not have
• Pictures of anybody with ear pieces.

```html
<!DOCTYPE html>
<html lang="en">
<head>
<meta charset="utf-8">
<title>Our Approach – Valdrin Insight</title>
<link href="https://fonts.googleapis.com/css2?family=Orbitron:wght@800;900&family=Mulish:wght@400;500;600;700;800&display=swap" rel="stylesheet">
<style>
  :root{
    --brand-red:#8b1a1f;
    --ink:#2b2b2b;
    --text:#3a3a3a;
    --muted:#8a8a8a;
    --panel:#f0f0f0;
    --dark-box:#2a2a2a;
    --mid-box:#7d7d7d;
    --accent-green:#6aab45;
    --rule:#d6d6d6;
    --white:#ffffff;
  }
  *{margin:0;padding:0;box-sizing:border-box}
  html,body{width:1200px;height:675px;overflow:hidden;background:var(--white)}
  body{font-family:"Mulish",Arial,sans-serif;color:var(--text);position:relative}

  .network-backdrop{position:absolute;left:0;top:0;width:1200px;height:400px;
    background:radial-gradient(ellipse at 50% 15%,#ececec 0%,#f7f7f7 50%,rgba(255,255,255,0) 100%)}

  .slide-title{position:absolute;left:82px;top:58px;font-family:"Orbitron",sans-serif;font-weight:900;
    font-size:27px;letter-spacing:1.5px;color:var(--brand-red)}

  .section-heading{position:absolute;top:140px;font-size:18px;font-weight:500;color:var(--ink)}
  .section-heading.approach{left:82px}
  .section-heading.services{left:923px}

  .source-panel{position:absolute;left:82px;top:172px;width:177px;height:335px;background:var(--panel)}
  .client-panel{position:absolute;left:273px;top:172px;width:148px;height:335px;background:var(--panel)}
  .panel-head{position:absolute;left:0;width:100%;text-align:center;font-size:13.5px;line-height:18px;color:var(--ink);font-weight:500}
  .source-panel .panel-head{top:5px}
  .client-panel .panel-head{top:25px}

  .step{position:absolute;display:flex;align-items:center;justify-content:center;text-align:center;
    color:var(--white);font-size:12.5px;line-height:15px}
  .step.source{left:16px;width:145px;height:37px;background:var(--dark-box)}
  .step.client{left:7px;width:132px;height:58px;background:var(--mid-box);padding:0 6px}
  .flow-arrow{position:absolute;left:249px;width:24px;height:36px}

  .intro-copy{position:absolute;left:437px;top:176px;width:466px;font-size:13.5px;line-height:18px}
  .intro-copy p{margin-bottom:7px}
  .intro-copy ul{list-style:none}
  .intro-copy li{position:relative;padding-left:17px;margin-bottom:7px}
  .intro-copy li::before{content:"•";position:absolute;left:2px;top:0}

  .column-rule{position:absolute;left:913px;top:136px;width:1px;height:371px;background:var(--rule)}

  .services-copy{position:absolute;left:923px;top:176px;width:222px;font-size:13.5px;line-height:18px}
  .services-copy p{margin-bottom:7px}
  .services-copy ul{list-style:none}
  .services-copy li{position:relative;padding-left:17px;margin-bottom:7px}
  .services-copy li svg{position:absolute;left:0;top:4px}

  .summary-band{position:absolute;left:82px;top:517px;width:1059px;height:82px;background:var(--brand-red);
    color:var(--white);font-weight:600;font-size:14.5px;line-height:18px;text-align:center;
    display:flex;align-items:center;justify-content:center;padding:0 52px}

  .confidential-notice{position:absolute;left:82px;top:628px;display:flex;align-items:center;gap:10px;
    font-size:10px;letter-spacing:0.8px;color:var(--muted);text-transform:uppercase}
  .confidential-notice strong{font-weight:800;color:var(--brand-red)}
  .confidential-notice .divider{width:1px;height:11px;background:var(--rule)}

  .brand-mark{position:absolute;left:1036px;top:628px;display:flex;align-items:center;gap:7px;
    font-weight:700;font-size:15px;color:var(--ink);letter-spacing:0.5px}
  .brand-mark .square{width:14px;height:14px;background:var(--brand-red)}
</style>
</head>
<body>
  <div class="network-backdrop" role="img" aria-label="Faint grey network of connected nodes as background texture"></div>

  <h1 class="slide-title">OUR APPROACH</h1>

  <h2 class="section-heading approach">Approach</h2>

  <div class="source-panel">
    <div class="panel-head">Publicly available<br>information and<br>non-traditional sources</div>
    <div class="step source" style="top:67px">Collection &amp; Analysis</div>
    <div class="step source" style="top:112px">Technology &amp; Tools</div>
    <div class="step source" style="top:157px">Professional<br>Analysts</div>
    <div class="step source" style="top:202px">Curated Intelligence</div>
    <div class="step source" style="top:247px">Vulnerability &amp; Risk</div>
    <div class="step source" style="top:292px">Finished Report</div>
  </div>

  <svg class="flow-arrow" style="top:375px" viewBox="0 0 24 36"><polygon points="0,0 24,18 0,36" fill="var(--accent-green)"/></svg>
  <svg class="flow-arrow" style="top:464px" viewBox="0 0 24 36"><polygon points="0,0 24,18 0,36" fill="var(--accent-green)"/></svg>

  <div class="client-panel">
    <div class="panel-head">Client</div>
    <div class="step client" style="top:67px">Ad hoc reporting</div>
    <div class="step client" style="top:134px">Continuous<br>monitoring</div>
    <div class="step client" style="top:202px">Threat reporting &amp;<br>landscape</div>
    <div class="step client" style="top:270px">Enhance proactive<br>security<br>operations</div>
  </div>

  <div class="intro-copy">
    <p>We scope and define client’s intelligence requirements and formulate a customized approach for relevant intelligence gathering, analysis, and reporting.</p>
    <ul>
      <li>Personal intelligence collection, monitoring, and security reporting</li>
      <li>Access surface and dark web content to conduct risk and vulnerability assessments specific to client intelligence requirements</li>
      <li>Provide relevant and up-to-date intelligence on threat actors and adversaries most likely to exploit or act against a client’s interest</li>
      <li>Help clients understand geopolitical trends and potential security risks to their personnel or organizations</li>
      <li>Conduct intelligence gathering on individuals to discover potential physical security risk, imminent harm or suspected criminal activity</li>
      <li>Conduct Technical OSINT for cyber vulnerabilities and risk assessments in the client’s mission space, research on cyber threat actors, their TTPs, and indicators of compromise</li>
    </ul>
  </div>

  <div class="column-rule"></div>

  <h2 class="section-heading services">Customized Services</h2>
  <div class="services-copy">
    <p>Tailored by design to support executives and high valued individuals.</p>
    <ul>
      <li><svg width="11" height="10" viewBox="0 0 11 10"><path d="M1 5.5 L4 8.5 L10 1" fill="none" stroke="var(--accent-green)" stroke-width="1.6"/></svg>Situational awareness and threat reporting</li>
      <li><svg width="11" height="10" viewBox="0 0 11 10"><path d="M1 5.5 L4 8.5 L10 1" fill="none" stroke="var(--accent-green)" stroke-width="1.6"/></svg>Supports executive travel planning and security</li>
      <li><svg width="11" height="10" viewBox="0 0 11 10"><path d="M1 5.5 L4 8.5 L10 1" fill="none" stroke="var(--accent-green)" stroke-width="1.6"/></svg>Personal brand detection and notification</li>
      <li><svg width="11" height="10" viewBox="0 0 11 10"><path d="M1 5.5 L4 8.5 L10 1" fill="none" stroke="var(--accent-green)" stroke-width="1.6"/></svg>Investigative services</li>
      <li><svg width="11" height="10" viewBox="0 0 11 10"><path d="M1 5.5 L4 8.5 L10 1" fill="none" stroke="var(--accent-green)" stroke-width="1.6"/></svg>Continuous threat monitoring</li>
      <li><svg width="11" height="10" viewBox="0 0 11 10"><path d="M1 5.5 L4 8.5 L10 1" fill="none" stroke="var(--accent-green)" stroke-width="1.6"/></svg>Ad hoc request for new intelligence requirements</li>
      <li><svg width="11" height="10" viewBox="0 0 11 10"><path d="M1 5.5 L4 8.5 L10 1" fill="none" stroke="var(--accent-green)" stroke-width="1.6"/></svg>Enhance security, protection, and privacy</li>
    </ul>
  </div>

  <div class="summary-band">Our experts conduct thorough intelligence assessments utilizing Open-Source Intelligence (OSINT) research and analysis. We help our clients prioritize and understand their vulnerabilities and risks with intelligence informed, actionable risk evaluation findings and develop long-term resiliency strategies.</div>

  <div class="confidential-notice"><strong>Confidential</strong><span class="divider"></span><span>For intended recipients only. Do not distribute.</span></div>

  <div class="brand-mark"><span class="square"></span>VALDRIN GROUP</div>
</body>
</html>
```